Quillbay.vc needs a better website design!

We need a new and better website for Quillbay.vc. We're a Canadian venture capital firm that invests in innovative entrepreneurs. We compete against the following websites: tormelo.vc, brightvalefund.ca, kestrowvc.com, and dovaran.vc. We're a diverse group of partners and we're dedicated to the founders we invest in.
Updates

I don’t really like stock photos of random people as part of the website design…so please try to stay away from using those images. Thanks, Owen

Target Market(s)

Canadian entrepreneurs and investors

Industry/Entity Type

Venture capital, finance, investment, entrepreneurship

Coding

Coded - Design and coding required

Number of Pages Required

4 page

Font styles to use
Sans Serif

Colors

Designer to choose colors to be used in the design.

Requirements
Must have
• Clean crisp overall design. Fast and to the point.
Nice to have
• Check out www.quillbay.vc - I did it myself and it is too basic and too wordy.
Should not have
• No stock images with random people in them! Not too wordy or with too many large images that are slow to load.

```html
<!DOCTYPE html>
<html lang="en">
<head>
<meta charset="utf-8">
<title>Quillbay.vc</title>
<link href="https://fonts.googleapis.com/css2?family=Poppins:wght@400;500;600&display=swap" rel="stylesheet">
<style>
:root{
  --green:#7c9a2f;
  --green-dark:#323f22;
  --ink:#1f2412;
  --text:#2b2f22;
  --muted:#6f6f6f;
  --line:#e4e4e4;
  --mint:#e6edd0;
  --white:#ffffff;
}
*{margin:0;padding:0;box-sizing:border-box}
html,body{width:1200px;height:2276px;overflow:hidden}
body{position:relative;font-family:'Poppins',sans-serif;color:var(--text);background:var(--white)}
.abs{position:absolute}

/* header */
.site-header{position:absolute;left:0;top:0;width:1200px;height:97px;background:var(--white);border-bottom:1px solid var(--line);z-index:3}
.brand{position:absolute;left:162px;top:34px;display:flex;align-items:center;gap:8px;font-weight:600;font-size:19px;color:var(--green);letter-spacing:.5px}
.brand-dot{width:22px;height:22px;border-radius:50%;background:var(--green)}
.nav{position:absolute;right:162px;top:0;display:flex;height:97px}
.nav a{display:flex;align-items:center;padding:0 13px;font-size:14px;color:#444;text-decoration:none;height:97px}
.nav a.active{background:#f2f2f2;color:var(--green);border-bottom:4px solid var(--green);padding-top:4px}

/* hero */
.hero{position:absolute;left:0;top:97px;width:1200px;height:580px;background:linear-gradient(180deg,#4b5a4a 0%,#3f5a35 40%,#2d4a22 75%,#20371a 100%)}
.hero-title{position:absolute;left:150px;top:134px;width:900px;text-align:center;color:var(--white);font-weight:500;font-size:29px;line-height:47px}
.numbers-label{position:absolute;left:0;top:330px;width:1200px;text-align:center;color:var(--white);font-size:19px}
.rule{position:absolute;top:343px;height:1px;background:rgba(255,255,255,.35)}
.stat{position:absolute;top:375px;width:165px;height:59px;border:1px solid rgba(255,255,255,.35);display:flex;align-items:center;justify-content:center;gap:7px;color:var(--white)}
.stat b{font-weight:500;font-size:38px;line-height:1}
.stat span{font-size:13.5px;line-height:15px}
.wave{position:absolute;left:0;top:570px;width:1200px;height:110px}

/* offer */
.section-title{position:absolute;left:0;width:1200px;text-align:center;font-weight:500;color:var(--ink)}
.offer-title{top:707px;font-size:27px;line-height:42px}
.dots{position:absolute;background:#f3f3f3;border-radius:4px}
.card{position:absolute;top:828px;width:420px;height:270px;background:var(--white);border:1px solid var(--line);border-radius:4px;box-shadow:0 2px 8px rgba(0,0,0,.06)}
.card svg{position:absolute;left:33px;top:50px}
.card p{position:absolute;left:33px;top:140px;width:370px;font-size:19.5px;line-height:32px;color:var(--text)}

/* portfolio */
.portfolio-title{top:1185px;font-size:26px}
.tile{position:absolute;width:154px;height:67px;border:1px solid #eee;border-radius:3px;box-shadow:0 2px 6px rgba(0,0,0,.05);display:flex;align-items:center;justify-content:center;gap:7px;font-weight:600;font-size:19px}
.tile i{width:12px;height:12px;border-radius:2px;display:block}

/* cta */
.cta{position:absolute;left:0;top:1511px;width:1200px;height:451px;background:var(--mint)}
.cta-art{position:absolute;left:680px;top:35px;width:330px;height:400px;background:radial-gradient(ellipse at center,#d3dfae 0%,rgba(211,223,174,0) 70%)}
.cta h2{position:absolute;left:207px;top:140px;font-weight:500;font-size:52px;line-height:63px;color:var(--ink)}
.cta p{position:absolute;left:207px;top:270px;font-size:26px;color:var(--ink)}

/* footer */
.site-footer{position:absolute;left:0;top:1962px;width:1200px;height:269px;background:var(--green-dark);color:var(--white)}
.footer-brand{position:absolute;left:162px;top:112px;display:flex;align-items:center;gap:10px;font-weight:600;font-size:28px;color:var(--green)}
.footer-brand i{width:34px;height:34px;border-radius:50%;background:var(--green);display:block}
.footer-col{position:absolute;top:58px}
.footer-col h3{font-weight:500;font-size:19px;margin-bottom:14px}
.footer-col li{list-style:none;font-size:13.5px;line-height:32px}
.footer-col li::before{content:"›";margin-right:10px}
.footer-col .mail{font-size:13.5px;margin-bottom:28px}
.social{display:flex;gap:7px}
.social i{width:30px;height:30px;border-radius:50%;background:#1fb4e6;display:block}
.copyright{position:absolute;left:0;top:2231px;width:1200px;height:45px;background:var(--green);color:var(--white);font-size:13.5px;display:flex;align-items:center;justify-content:center}
</style>
</head>
<body>

<header class="site-header">
  <div class="brand"><span class="brand-dot"></span>QUILLBAY.VC</div>
  <nav class="nav">
    <a class="active" href="#">Team</a>
    <a href="#">Companies</a>
    <a href="#">What We Look For</a>
  </nav>
</header>

<section class="hero" role="img" aria-label="Misty green mountain valley landscape">
  <h1 class="hero-title">Quillbay.vc is a venture capital firm that invests in innovative seed-stage technology companies in Western Canada focused on B2B and SaaS markets.</h1>
  <div class="rule" style="left:262px;width:212px"></div>
  <div class="numbers-label">Quillbay.vc in numbers</div>
  <div class="rule" style="left:723px;width:210px"></div>
  <div class="stat" style="left:333px"><b>10</b><span>Portfolio<br>companies</span></div>
  <div class="stat" style="left:517px"><b>7</b><span>Follow-on<br>financings</span></div>
  <div class="stat" style="left:702px"><b>100</b><span>+<br>Employees</span></div>
</section>
<svg class="wave" viewBox="0 0 1200 110" preserveAspectRatio="none" aria-hidden="true">
  <path d="M0 62 C120 20 240 5 360 22 C520 45 620 100 760 97 C900 94 1060 82 1200 58 L1200 110 L0 110 Z" fill="#ffffff"/>
</svg>

<h2 class="section-title offer-title">We are serial entrepreneurs and venture<br>capital investors who provide</h2>
<div class="dots" role="img" aria-label="Faint dotted decoration" style="left:968px;top:802px;width:100px;height:98px"></div>
<div class="dots" role="img" aria-label="Faint dotted decoration" style="left:133px;top:1022px;width:100px;height:98px"></div>

<div class="card" style="left:162px">
  <svg width="82" height="78" viewBox="0 0 82 78" fill="none" stroke-width="2.5">
    <path d="M5 33 C25 30 40 20 58 4" stroke="#7c9a2f"/>
    <path d="M50 3 L59 3 L58 12" stroke="#7c9a2f"/>
    <rect x="2" y="58" width="14" height="18" stroke="#8a8a8a"/>
    <rect x="24" y="46" width="14" height="30" stroke="#8a8a8a"/>
    <rect x="46" y="30" width="14" height="46" stroke="#8a8a8a"/>
    <rect x="66" y="14" width="14" height="62" stroke="#8a8a8a"/>
  </svg>
  <p>Mentoring and strategic advice to help you grow your company quickly and efficiently</p>
</div>
<div class="card" style="left:619px">
  <svg width="72" height="78" viewBox="0 0 72 78" fill="none" stroke-width="2.5">
    <circle cx="23" cy="13" r="11" stroke="#8a8a8a"/>
    <path d="M2 68 L2 44 C2 34 12 30 23 30 C34 30 42 34 44 40" stroke="#8a8a8a"/>
    <path d="M2 68 L34 68" stroke="#8a8a8a"/>
    <circle cx="50" cy="55" r="19" stroke="#7c9a2f"/>
    <path d="M56 46 C52 43 44 44 44 49 C44 55 57 53 57 60 C57 65 48 66 43 63 M50 40 L50 70" stroke="#7c9a2f"/>
  </svg>
  <p>Investor introductions to help you raise additional follow-on funding for your startup</p>
</div>

<h2 class="section-title portfolio-title">Check out our innovative portfolio companies!</h2>
<div class="tile" style="left:162px;top:1259px;color:#1d1d1d"><i style="background:#a8a4ef"></i>Tidelock</div>
<div class="tile" style="left:342px;top:1259px;color:#7bb6b0;font-weight:400;letter-spacing:3px;font-size:16px">MARROWFEN</div>
<div class="tile" style="left:523px;top:1259px;color:#222">Loftsail</div>
<div class="tile" style="left:703px;top:1259px;color:#111;font-size:21px">BREVANT</div>
<div class="tile" style="left:885px;top:1259px;color:#666;font-weight:400;font-size:22px">Ostrel<i style="background:#e6582a;width:8px;height:8px"></i></div>
<div class="tile" style="left:162px;top:1348px;color:#333;font-weight:500;font-size:16px;letter-spacing:1px">CINDERVALE</div>
<div class="tile" style="left:342px;top:1348px;color:#1b2a55;font-size:21px"><i style="background:#e2459a"></i>HALVIX</div>
<div class="tile" style="left:523px;top:1348px;color:#666;font-weight:400;font-size:21px">Quenly<i style="background:#7fd0c4;border-radius:50%;width:18px;height:18px"></i></div>
<div class="tile" style="left:703px;top:1348px;color:#222;font-weight:400;font-size:15px">Pellwick</div>
<div class="tile" style="left:885px;top:1348px;color:#1a1a1a">Norrabel</div>

<section class="cta">
  <div class="cta-art" role="img" aria-label="Faint sprouting plant illustration"></div>
  <h2>If you have what<br>we’re looking for</h2>
  <p>Contact us today</p>
</section>

<footer class="site-footer">
  <div class="footer-brand"><i></i>QUILLBAY.VC</div>
  <div class="footer-col" style="left:544px">
    <h3>Quick Links</h3>
    <ul><li>Home</li><li>What</li><li>Who</li><li>Portfolio</li></ul>
  </div>
  <div class="footer-col" style="left:852px">
    <h3>Get In Touch</h3>
    <div class="mail">info@quillbay.vc</div>
    <h3>Follow Us</h3>
    <div class="social"><i></i><i style="background:#1791c4"></i></div>
  </div>
</footer>
<div class="copyright">Copyright © 2021 Quillbay.vc - All Rights Reserved.</div>

</body>
</html>
```